GTP biz card

We need a business card design for our new company based in Los Angeles called "Gold Tide Pictures". We develop film and television projects. We work with investors, financiers, film production companies, film distribution and sales companies as well as studios. We would like to incorporate our logo (see attached) on a two-sided card. We need to include: name and title, address, phone, email and company website.

Target Market(s)

Business, financial and studio clients

Industry/Entity Type

Business

Contact Information for Business Card

Two-sided. We are thinking of the logo on one side and the information on the back. Please feel free to be creative! Thanks.

Requirements
Must have
• Please include the following text information, excluding the "CAPS CATEGORY:" and please allow the ability for us to change the name, title and email address for each company employee):
• NAME & TITLE:
• Neil Parker
• Managing Partner
• COMPANY NAME:
• GOLD TIDE PICTURES (please use existing logo)
• COMPANY ADDRESS:
• KTW Studio Park
• 2250 Halverd Street
• Harbor Wing, 4th Floor
• Manhattan Beach, CA 90412
• COMPANY PHONE NUMBER:
• 310-555-0148
• COMPANY WEBSITE ADDRESS:
• www.goldtidepicturesgroup.example
• EMAIL ADDRESS: (only one per card)
• peter@goldtidepicturesgroup.example
• bingo@goldtidepicturesgroup.example
• neil@goldtidepicturesgroup.example

```html
<!DOCTYPE html>
<html lang="en">
<head>
<meta charset="utf-8">
<title>Gold Tide Pictures – Business Card</title>
<link rel="stylesheet" href="https://fonts.googleapis.com/css2?family=Lato:wght@400;700;900&display=swap">
<style>
  :root {
    --backdrop: #2a2a2c;
    --card: #070708;
    --card-edge: #1a1a1c;
    --accent: #29a9cf;
    --accent-soft: #8fd3ea;
    --mark: #1f8fbf;
    --text-light: #e6e6e6;
    --text-muted: #bdbdbd;
    --divider-top: #0b0b0c;
    --divider-mid: #9fd8ea;
  }
  * { box-sizing: border-box; margin: 0; padding: 0; }
  html, body {
    width: 1200px; height: 900px; overflow: hidden;
    background: var(--backdrop);
    font-family: "Lato", Arial, sans-serif;
  }
  .canvas { position: relative; width: 1200px; height: 900px; }

  .card {
    position: absolute;
    background: var(--card);
    border: 1px solid var(--card-edge);
    box-shadow: 0 18px 40px rgba(0,0,0,0.6);
  }
  .card--front { left: 70px; top: 60px; width: 620px; height: 354px; }
  .card--back  { left: 490px; top: 470px; width: 660px; height: 377px; }

  .brand {
    position: absolute;
    display: flex; flex-direction: column; align-items: center;
  }
  .brand__dot {
    width: 96px; height: 96px; border-radius: 50%;
    background: var(--mark);
  }
  .brand__name {
    margin-top: 26px;
    font-weight: 900; font-size: 30px; letter-spacing: 2px;
    color: var(--accent-soft);
    white-space: nowrap;
  }
  .card--front .brand { left: 0; right: 0; top: 78px; }

  .card--back .brand { left: 30px; width: 300px; top: 88px; }
  .card--back .brand__dot { width: 86px; height: 86px; }
  .card--back .brand__name { font-size: 24px; margin-top: 24px; }

  .divider {
    position: absolute; left: 346px; top: 30px; width: 2px; height: 320px;
    background: linear-gradient(var(--divider-top), var(--divider-mid) 55%, var(--divider-top));
  }

  .contact { position: absolute; left: 372px; top: 36px; right: 16px; }
  .contact__name {
    font-weight: 900; font-size: 22px; color: var(--accent); letter-spacing: 0.3px;
  }
  .contact__title {
    font-weight: 700; font-size: 14px; color: var(--text-light); margin-top: 2px;
  }
  .contact__address {
    margin-top: 34px;
    font-weight: 700; font-size: 15px; line-height: 1.35; color: var(--accent);
    font-style: normal;
  }
  .contact__list { list-style: none; margin-top: 16px; }
  .contact__item {
    display: flex; align-items: center; gap: 10px;
    font-size: 14px; color: var(--text-muted); margin-bottom: 11px;
    white-space: nowrap;
  }
  .contact__icon { width: 16px; height: 14px; flex: none; }
  .contact__web { font-weight: 700; color: var(--text-light); font-size: 15px; }
</style>
</head>
<body>
<main class="canvas">

  <section class="card card--front" aria-label="Card front">
    <div class="brand">
      <span class="brand__dot" aria-hidden="true"></span>
      <span class="brand__name">GOLD TIDE PICTURES</span>
    </div>
  </section>

  <section class="card card--back" aria-label="Card back">
    <div class="brand">
      <span class="brand__dot" aria-hidden="true"></span>
      <span class="brand__name">GOLD TIDE PICTURES</span>
    </div>

    <span class="divider" aria-hidden="true"></span>

    <div class="contact">
      <p class="contact__name">NEIL PARKER</p>
      <p class="contact__title">Managing Partner</p>
      <address class="contact__address">KTW Studio Park<br>2250 Halverd Street<br>Harbor Wing, 4th Floor<br>Manhattan Beach, CA 90412</address>
      <ul class="contact__list">
        <li class="contact__item">
          <svg class="contact__icon" viewBox="0 0 16 14" aria-hidden="true">
            <path d="M1 4 Q8 -1 15 4 L13 6 L11 4.5 L5 4.5 L3 6 Z" fill="#bdbdbd"/>
            <rect x="3" y="7" width="10" height="6" rx="1" fill="#bdbdbd"/>
          </svg>
          <span>310-555-0148</span>
        </li>
        <li class="contact__item">
          <svg class="contact__icon" viewBox="0 0 16 14" aria-hidden="true">
            <rect x="1" y="2" width="14" height="10" fill="none" stroke="#bdbdbd" stroke-width="1.4"/>
            <path d="M1 2 L8 8 L15 2" fill="none" stroke="#bdbdbd" stroke-width="1.4"/>
          </svg>
          <span>neil@goldtidepicturesgroup.example</span>
        </li>
        <li class="contact__item contact__web">www.goldtidepicturesgroup.example</li>
      </ul>
    </div>
  </section>

</main>
</body>
</html>
```